wealth management firm, professional group, new model

we have a logo that works but we need a card, white background using our colors...clean look

our tag line if can be used in

Guiding Clients Toward Ownership

```html
<!DOCTYPE html>
<html lang="it">
<head>
<meta charset="utf-8">
<title>Varco Capital Advisors – Business Card</title>
<link href="https://fonts.googleapis.com/css2?family=Montserrat:wght@400;500&family=Raleway:wght@700&display=swap" rel="stylesheet">
<style>
  :root {
    --navy: #23395d;
    --ink: #4a4f57;
    --paper: #f7f7f5;
    --backdrop: #e4e4e4;
  }
  * { margin: 0; padding: 0; box-sizing: border-box; }
  html, body {
    width: 1200px; height: 800px; overflow: hidden;
    background: var(--backdrop);
    font-family: "Montserrat", sans-serif;
    color: var(--navy);
  }
  .canvas { position: relative; width: 1200px; height: 800px; }
  .card {
    position: absolute; left: 405px; width: 400px; height: 259px;
    background: var(--paper);
  }
  .card--back { top: 113px; }
  .card--front { top: 438px; }

  /* Back: brand + contact */
  .brand-small {
    position: absolute; left: 30px; width: 180px; top: 118px;
    text-align: center;
  }
  .brand-small .wordmark {
    font-size: 24px; font-weight: 500; letter-spacing: 2px;
    margin-right: -2px; line-height: 1;
  }
  .brand-small .descriptor {
    margin-top: 12px; font-size: 9px; letter-spacing: 1.2px; font-weight: 500;
  }
  .divider {
    position: absolute; left: 211px; top: 74px; width: 1px; height: 111px;
    background: var(--navy);
  }
  .contact { position: absolute; left: 226px; top: 74px; }
  .contact .name {
    font-family: "Raleway", sans-serif; font-weight: 700;
    font-size: 12px; letter-spacing: -0.1px; line-height: 14px;
  }
  .contact .role { font-size: 9.5px; color: var(--ink); line-height: 11px; }
  .contact-line {
    position: absolute; left: 0; display: flex; align-items: flex-start;
    font-size: 9.5px; color: var(--ink); line-height: 11.5px; white-space: nowrap;
  }
  .contact-line svg {
    width: 10px; height: 10px; margin-right: 5px; margin-top: 0.5px;
    flex: none; stroke: var(--navy); fill: none; stroke-width: 0.9;
  }
  .contact-line--address { top: 36px; }
  .contact-line--phone { top: 71px; }
  .contact-line--email { top: 85px; }
  .contact-line--web { top: 99px; }

  /* Front: brand + tagline */
  .brand-large {
    position: absolute; left: 0; right: 0; top: 98px; text-align: center;
  }
  .brand-large .wordmark {
    font-size: 42px; font-weight: 500; letter-spacing: 4px;
    margin-right: -4px; line-height: 1;
  }
  .brand-large .descriptor {
    margin-top: 20px; font-size: 14px; letter-spacing: 2px; font-weight: 500;
  }
  .rule {
    position: absolute; left: 168px; top: 193px; width: 64px; height: 1px;
    background: var(--navy);
  }
  .tagline {
    position: absolute; left: 0; right: 0; top: 207px; text-align: center;
    font-size: 10px; letter-spacing: 1.6px; font-weight: 500;
    text-transform: uppercase;
  }
</style>
</head>
<body>
<div class="canvas">

  <section class="card card--back">
    <div class="brand-small">
      <div class="wordmark">VARCO</div>
      <div class="descriptor">CAPITAL ADVISORS</div>
    </div>
    <div class="divider"></div>
    <div class="contact">
      <div class="name">MARCO DELUCA</div>
      <div class="role">CEO e Fondatore</div>

      <div class="contact-line contact-line--address">
        <svg viewBox="0 0 10 10"><path d="M5 9.5 C2.5 6.5 1.8 5 1.8 3.6 A3.2 3.2 0 0 1 8.2 3.6 C8.2 5 7.5 6.5 5 9.5 Z"/><circle cx="5" cy="3.6" r="1.1"/></svg>
        <span>Via Solari<br>14 20144 Milano</span>
      </div>
      <div class="contact-line contact-line--phone">
        <svg viewBox="0 0 10 10"><path d="M2.2 1 L3.8 2.8 L3 4 C3.6 5.3 4.7 6.4 6 7 L7.2 6.2 L9 7.8 L8 9 C4.5 8.8 1.2 5.5 1 2 Z"/><path d="M6 1.2 A3 3 0 0 1 8.8 4"/></svg>
        <span>+39.345.610.2870</span>
      </div>
      <div class="contact-line contact-line--email">
        <svg viewBox="0 0 10 10"><rect x="0.8" y="2" width="8.4" height="6"/><path d="M0.8 2 L5 5.5 L9.2 2 M0.8 8 L3.8 4.8 M9.2 8 L6.2 4.8"/></svg>
        <span>info@varcomail.com</span>
      </div>
      <div class="contact-line contact-line--web">
        <svg viewBox="0 0 10 10"><circle cx="5" cy="5" r="4.2"/><ellipse cx="5" cy="5" rx="1.8" ry="4.2"/><path d="M0.8 5 H9.2 M1.5 3 H8.5 M1.5 7 H8.5"/></svg>
        <span>www.varcoweb.com</span>
      </div>
    </div>
  </section>

  <section class="card card--front">
    <div class="brand-large">
      <div class="wordmark">VARCO</div>
      <div class="descriptor">CAPITAL ADVISORS</div>
    </div>
    <div class="rule"></div>
    <p class="tagline">Guiding Clients Toward Ownership</p>
  </section>

</div>
</body>
</html>
```